Wordpress Business Travel Blog and Discussion Board

Oh, Hello!

We are looking for a motivated designer to create a full, turnkey interactive WordPress website geared toward business travel that includes a news style blog (look at ByteHarbor.com and Wirevane.com for the style we like) that is seamlessly integrated with a robust message board (look at GateBanter.com and RoamLedger.com). Ok, so stick with us here because this is actually a pretty cool project that shouldn't be too hard, but yes, of course we have some curve balls that we are throwing your way. Sorry! :)

*On the front page*

- We would like to have a typical news style blog layout that is fun, somewhat professional, and easy to read. That's easy!

- Somewhere within first glance, we would like to have a short list of the most active discussions on our discussion board. (What's trending, or something like that). Not too bad, right?

- Overall, want to have a good amount of content, but we also do not want the visitor to feel as if he or she is having to sift through a lot of content to see what he or she wants to see. Great! We're past the beginning!

We will have traditional visual advertising on all of our pages. Please leave space as necessary :)

*On the Blog/News story pages*

Let's keep these simple - but there is a twist!

Let's say I create a blog/news post. I would like that blog/news post to also be opened as a discussion on the discussion board. For example, I write an article about Coastal Skyways and their service on a particular international flight. This will be opened as a discussion under the Coastal Skyways topic in the discussion board. Other users can also open new discussions under any topic on the discussion board, but they cannot post stories (unless permission is given) to the blog wall. We would like their posts to show up as regular discussion board posts while the news/blog posts by us show up as news/blog posts on the front page, *and* (oh yes we did!) as discussions in the discussion board. Of course, users will still be able to post comments to the news/blog post, which will also be posted in the discussion.

OK, does that make sense? Let me know if I can help make this more clear! :) Sorry!

*Wiki Pages*

Take a look at the Coastal Skyways example above. In that example, my news/blog entry automatically opens a new discussion post. Although we won't necessarily need to create a new wiki page, we would like to tag the post and the discussion to a wiki page about the topic. The wiki page can be created and edited by all users (and locked by us if necessary). BONUS! Can we tag more than one wiki page?

*Websites that inspire us*

ByteHarbor.com - concept and design
Wirevane.com - concept and design
GateBanter.com - concept
RoamLedger.com - concept
pomwhispers.com - concept

All of the sites above are great and we can only thrive with their great success. We are not aiming to be a competitor to the travel sites, but just another great option for interested visitors. Please do not simply copy what they have. What is posted above is a list of our favorite sites that we visit every day.

Our favorite font is Segoe UI, but please don't use this (or a similar font) too much! Maybe just titles would be great. You're the designer so you can make the call here.

Also, our favorite color is blue, but if you have another favorite color, go ahead and show us what you can do! (Don't use too much blue!)

*Oh, and One More Thing*

(I know, you thought we were done. We're not!)

Here's the killer - We would like to create a way for people to, say, enter the details of their next trip and be matched with someone who will also be on a portion of their trip.

For example, let's say I am flying Meridian Airways flight 109 from Los Angeles to New York JFK Airport this Friday. I am staying at the Bellcourt New York Times Square on Friday night, and I am flying back on Saturday night on Kestrel flight 290 from New York JFK airport back to Los Angeles. Another user will also be on the Kestrel flight back to Los Angeles with me and he entered that information in the website. (Note, the user has to manually enter this information). The other user and I will both be notified that there is at least one other user who will be on the same Kestrel flight as me. We will both have the option to reveal our online identity - which will in fact be released to each person as long as each person *mutually* agrees.

This can be very simple - almost like a dating site type of match but it is based on two people being in the same place at the same time (based on what they report). Also, we would like to be able to collect this information - not necessarily tied to the user's true identity. The information we would like to have is - what the user is claiming he or she is doing on the trip (i.e. staying at the Bellcourt Times Square, flying Meridian Airways), and whether or not the user agreed to reveal his or her identity - AND! whether or not the users both revealed their identity.

*Most Important*

HAVE FUN and THANK YOU!! :)

A couple of quick notes - this is a design and code project. We are most likely offering a more $(!) design and code project for the version 2.0 of this website once we get user feedback from this first round.

Also, the name of the website is Jaunta. (www.jaunta-example.com)

Good luck!

Reason: Extending as requested by a few designers. Only 3 more days to get your designs in!

Reason: All designs look great! Last chance for one or two more designers who have requested an extension. All designs that were already submitted on time will be considered with much higher priority. Thank you!

Requirements
Must have
• We need to have a high end, professional, modern, and clean design on the front page to entice readers to constantly visit and stay on our site.
Nice to have
• It would be great to give us the ability to automatically recognize users for visiting the website and/or participating and commenting. Social badges, recognition, etc. would be very cool.
Should not have
• Although this is a website around business travel, we do not necessarily want it to be business travel themed. There can be hints of the theme, but otherwise the visual look should be somewhat generic.

```html
<!DOCTYPE html>
<html lang="en">
<head>
<meta charset="utf-8">
<title>Tarrow Travels</title>
<link href="https://fonts.googleapis.com/css2?family=Oswald:wght@300;400&display=swap" rel="stylesheet">
<style>
  :root {
    --page-bg: #aaa892;
    --page-glow: #f4f3ee;
    --ink: #4a4a42;
    --ink-soft: #555;
    --body-ink: #333;
    --panel: #edebec;
    --panel-line: #c9c6c4;
    --copper-top: #b06f55;
    --copper-mid: #96553d;
    --copper-tip: #e59a78;
    --bar: #efeee8;
    --button: #dcdbd8;
    --badge: #8c8c8c;
    --photo-sky: #6fa6d6;
    --photo-sand: #d8c6aa;
    --photo-building: #c57a4c;
    --social: #2b2b2b;
    --heading: "Oswald", "Arial Narrow", sans-serif;
    --text: Arial, Helvetica, sans-serif;
  }
  * { box-sizing: border-box; margin: 0; padding: 0; }
  html, body { width: 1063px; height: 1200px; overflow: hidden; }
  body {
    position: relative;
    font-family: var(--text);
    color: var(--body-ink);
    background: radial-gradient(ellipse 520px 220px at 530px 40px, var(--page-glow) 0%, #d9d8cc 55%, var(--page-bg) 100%);
  }
  .abs { position: absolute; }
  h1, h2, h3, .tab, .main-nav a, .top-links span { white-space: nowrap; }

  .top-links { top: 5px; left: 770px; font-family: var(--heading); font-weight: 300; font-size: 13px; color: var(--ink); }
  .top-links span { position: absolute; }

  .brand { top: 20px; left: 0; width: 1076px; text-align: center; font-family: var(--heading); font-weight: 400; font-size: 40px; color: var(--ink); }

  .ribbon { top: 107px; left: 58px; }
  .main-nav { top: 107px; left: 89px; width: 886px; height: 71px; background: linear-gradient(#f6f5f0, #e6e4dc); box-shadow: 0 2px 4px rgba(0,0,0,.25); }
  .main-nav a { position: absolute; top: 27px; font-family: var(--heading); font-weight: 300; font-size: 14px; color: var(--ink); text-decoration: none; }
  .nav-sep { position: absolute; top: 28px; width: 1px; height: 14px; background: #b9b6ac; }
  .search { position: absolute; top: 24px; left: 698px; width: 173px; height: 19px; background: #fff; border: 1px solid #dcdad3; font-size: 11px; color: #666; padding: 3px 5px; }

  .hero-photo { top: 179px; left: 101px; width: 595px; height: 316px; background: linear-gradient(180deg, var(--photo-sky) 0%, #a9cbe0 40%, #e9e4d8 70%, var(--photo-sand) 100%); }
  .hero-panel { top: 179px; left: 696px; }
  .hero-title { top: 210px; left: 713px; width: 232px; font-family: var(--heading); font-weight: 400; font-size: 24px; line-height: 30px; color: #fff; letter-spacing: -.4px; }
  .hero-copy { top: 246px; left: 714px; width: 230px; font-size: 12.2px; line-height: 14.6px; color: #fff; text-align: justify; }

  .content { top: 495px; left: 101px; width: 864px; height: 586px; background: var(--panel); }

  .tab { background: var(--panel); border: 1px solid var(--panel-line); border-bottom: none; font-family: var(--heading); font-weight: 400; color: var(--ink); }
  .topics-tab { top: 520px; left: 105px; width: 115px; height: 31px; font-size: 17px; line-height: 28px; padding-left: 11px; z-index: 2; }
  .topics-box { top: 550px; left: 105px; width: 589px; height: 520px; border: 1px solid var(--panel-line); }

  .post-img { width: 220px; height: 97px; background: linear-gradient(100deg, var(--photo-sky) 0%, #9fc4e6 45%, var(--photo-building) 70%, #a9643c 100%); }
  .post-title { font-family: var(--heading); font-weight: 300; font-size: 16px; color: var(--ink); }
  .post-meta { font-size: 11px; color: var(--body-ink); }
  .post-body { width: 342px; font-size: 11px; line-height: 12.8px; text-align: justify; color: #3a3a3a; }
  .badge { width: 27px; height: 23px; background: var(--badge); color: #fff; font-size: 13px; text-align: center; line-height: 23px; }
  .badge::after { content: ""; position: absolute; left: 4px; bottom: -5px; border-left: 5px solid var(--badge); border-bottom: 5px solid transparent; }
  .read-more { width: 82px; height: 28px; background: var(--button); border-radius: 5px; box-shadow: inset 0 1px 0 #fff, 0 1px 1px rgba(0,0,0,.15); font-size: 12px; font-weight: bold; color: #666; text-align: center; line-height: 28px; }
  .post-rule { left: 114px; width: 573px; height: 1px; background: #bdbab6; }

  .newsletter-title { top: 576px; left: 700px; width: 265px; text-align: center; font-family: var(--heading); font-weight: 400; font-size: 15.5px; color: var(--ink); }
  .newsletter-input { top: 601px; left: 739px; width: 169px; height: 21px; background: #fff; border: 1px solid #cfccc7; border-radius: 3px; }
  .subscribe { top: 633px; left: 791px; width: 75px; height: 22px; background: #cfcdca; border-radius: 3px; font-family: var(--heading); font-size: 12px; color: var(--ink); text-align: center; line-height: 22px; }

  .side-tab { top: 680px; height: 31px; font-size: 13px; line-height: 30px; text-align: center; z-index: 2; }
  .side-box { top: 710px; left: 709px; width: 250px; height: 360px; border: 1px solid var(--panel-line); }
  .side-img { left: 717px; width: 68px; height: 61px; background: linear-gradient(100deg, var(--photo-sky) 0%, #9fc4e6 35%, var(--photo-building) 65%, #a9643c 100%); }
  .side-title { left: 791px; font-family: var(--heading); font-weight: 300; font-size: 14px; color: var(--ink); }
  .side-text { left: 793px; width: 150px; font-size: 11px; line-height: 13px; color: #333; }
  .side-rule { left: 733px; width: 193px; border-top: 1px dashed #b6b3ae; }
  .see-all { top: 1051px; left: 918px; font-size: 11px; color: #333; text-decoration: underline; }

  .footer-bar { top: 1083px; left: 100px; width: 865px; height: 39px; background: linear-gradient(#dfddd6, #f1f0ec); border-bottom: 4px solid #f7f7f4; }
  .footer-bar span { position: absolute; top: 13px; font-size: 11px; color: #666; white-space: nowrap; }
  .social { width: 26px; height: 26px; border-radius: 50%; background: var(--social); top: 1089px; }
  .copyright { top: 1132px; left: 700px; width: 257px; text-align: right; font-size: 10.5px; color: #555; }
</style>
</head>
<body>

  <nav class="abs top-links" aria-label="Account">
    <span style="left:10px">SIGNIN</span>
    <span style="left:61px">REGISTER</span>
    <span style="left:127px">HELP</span>
    <span style="left:174px">FAQ</span>
  </nav>

  <div class="abs brand">Tarrow Travels</div>

  <svg class="abs ribbon" width="950" height="85" viewBox="0 0 950 85" aria-hidden="true">
    <polygon points="0,10 40,10 40,82 8,82 14,46" fill="#e7e5dc"/>
    <polygon points="950,10 910,10 910,82 942,82 936,46" fill="#e7e5dc"/>
  </svg>

  <nav class="abs main-nav" aria-label="Main">
    <a style="left:28px">HOME</a><i class="nav-sep" style="left:75px"></i>
    <a style="left:94px">ABOUT</a><i class="nav-sep" style="left:149px"></i>
    <a style="left:171px">BLOG</a><i class="nav-sep" style="left:214px"></i>
    <a style="left:234px">FORUMS</a><i class="nav-sep" style="left:294px"></i>
    <a style="left:314px">SERVICES</a><i class="nav-sep" style="left:377px"></i>
    <a style="left:394px">CITIES</a><i class="nav-sep" style="left:440px"></i>
    <a style="left:458px">FAQ</a><i class="nav-sep" style="left:493px"></i>
    <a style="left:511px">TESTIMONIALS</a><i class="nav-sep" style="left:595px"></i>
    <a style="left:612px">CONTACT</a>
    <div class="search">Search
      <svg style="position:absolute;right:6px;top:2px" width="13" height="13" viewBox="0 0 13 13" aria-hidden="true"><circle cx="5" cy="5" r="4" fill="none" stroke="#555" stroke-width="1.5"/><line x1="8" y1="8" x2="12" y2="12" stroke="#555" stroke-width="1.6"/></svg>
    </div>
  </nav>

  <div class="abs content"></div>

  <div class="abs hero-photo" role="img" aria-label="Photo of a family holding hands and playing on a sunny beach"></div>

  <svg class="abs hero-panel" width="269" height="368" viewBox="0 0 269 368" aria-hidden="true">
    <defs>
      <linearGradient id="copper" x1="0" y1="0" x2="0" y2="1">
        <stop offset="0" stop-color="#b06f55"/>
        <stop offset="1" stop-color="#96553d"/>
      </linearGradient>
      <linearGradient id="copperTip" x1="0" y1="0" x2="0" y2="1">
        <stop offset="0" stop-color="#a8644a"/>
        <stop offset="1" stop-color="#e59a78"/>
      </linearGradient>
    </defs>
    <polygon points="0,316 269,312 269,320 134,368 0,320" fill="url(#copperTip)"/>
    <polygon points="0,0 269,0 269,268 134,320 0,268" fill="url(#copper)"/>
    <polygon points="0,268 134,320 269,268 269,312 134,368 0,316" fill="url(#copperTip)" opacity=".9"/>
    <g fill="#d8907a" stroke="#8a4a34" stroke-width="1">
      <circle cx="99" cy="291" r="6.5"/><circle cx="118" cy="291" r="6.5"/>
      <circle cx="138" cy="291" r="6.5"/><circle cx="157" cy="291" r="6.5"/>
    </g>
  </svg>
  <h1 class="abs hero-title">THINGS TO DO IN EUROPE</h1>
  <p class="abs hero-copy">Lorem ipsum dolor sit amet, consectetur adipiscing elit. Sed blandit massa vel mauris sollicitudin dignissim. Phasellus ultrices tellus eget ipsum ornare molestie scelerisque eros dignissim. Phasellus fringilla hendrerit lectus nec vehicula. Pellentesque habitant morbi tristique senectus et netus et malesuada fames ac turpis egestas. In faucibus, risus eu volutpat pellentesque, massa felis feugiat velit, nec mattis felis elit a eros.</p>

  <section aria-label="Latest topics">
    <div class="abs tab topics-tab">LATEST TOPICS</div>
    <div class="abs topics-box"></div>

    <article>
      <div class="abs post-img" style="top:581px;left:113px" role="img" aria-label="Photo of a curved hotel building with beach umbrellas under a blue sky"></div>
      <h2 class="abs post-title" style="top:576px;left:342px">ANCIENT ROME - VISIT TODAY</h2>
      <p class="abs post-meta" style="top:600px;left:342px">By Admin on July 14, 2011 in Adipisicing</p>
      <p class="abs post-body" style="top:618px;left:342px">Lorem ipsum dolor sit amet, consectetur adipiscing elit. Sed blandit massa vel mauris sollicitudin dignissim. Phasellus ultrices tellus eget ipsum ornare molestie scelerisque eros dignissim. Phasellus fringilla hendrerit lectus nec vehicula. Pellentesque habitant morbi tristique senectus et netus et malesuada fames ac</p>
      <div class="abs badge" style="top:685px;left:560px">3</div>
      <div class="abs read-more" style="top:683px;left:601px">Read more</div>
    </article>
    <div class="abs post-rule" style="top:720px"></div>

    <article>
      <div class="abs post-img" style="top:741px;left:114px" role="img" aria-label="Photo of a curved hotel building with beach umbrellas under a blue sky"></div>
      <h2 class="abs post-title" style="top:736px;left:343px">ANCIENT ROME - VISIT TODAY</h2>
      <p class="abs post-meta" style="top:760px;left:343px">By Admin on July 14, 2011 in Adipisicing</p>
      <p class="abs post-body" style="top:778px;left:343px">Lorem ipsum dolor sit amet, consectetur adipiscing elit. Sed blandit massa vel mauris sollicitudin dignissim. Phasellus ultrices tellus eget ipsum ornare molestie scelerisque eros dignissim. Phasellus fringilla hendrerit lectus nec vehicula. Pellentesque habitant morbi tristique senectus et netus et malesuada fames ac</p>
      <div class="abs badge" style="top:845px;left:561px">3</div>
      <div class="abs read-more" style="top:843px;left:602px">Read more</div>
    </article>
    <div class="abs post-rule" style="top:886px"></div>

    <article>
      <div class="abs post-img" style="top:906px;left:114px" role="img" aria-label="Photo of a curved hotel building with beach umbrellas under a blue sky"></div>
      <h2 class="abs post-title" style="top:901px;left:343px">ANCIENT ROME - VISIT TODAY</h2>
      <p class="abs post-meta" style="top:925px;left:343px">By Admin on July 14, 2011 in Adipisicing</p>
      <p class="abs post-body" style="top:943px;left:343px">Lorem ipsum dolor sit amet, consectetur adipiscing elit. Sed blandit massa vel mauris sollicitudin dignissim. Phasellus ultrices tellus eget ipsum ornare molestie scelerisque eros dignissim. Phasellus fringilla hendrerit lectus nec vehicula. Pellentesque habitant morbi tristique senectus et netus et malesuada fames ac</p>
      <div class="abs badge" style="top:1011px;left:561px">3</div>
      <div class="abs read-more" style="top:1009px;left:602px">Read more</div>
    </article>
  </section>

  <aside aria-label="Sidebar">
    <h2 class="abs newsletter-title">SUBSCRIBE FOR NEWLETTER</h2>
    <div class="abs newsletter-input"></div>
    <div class="abs subscribe">SUBSCRIBE</div>

    <div class="abs tab side-tab" style="left:709px;width:86px">RECENT POSTS</div>
    <div class="abs tab side-tab" style="left:798px;width:87px">LATEST TWEETS</div>
    <div class="abs side-box"></div>

    <div class="abs side-img" style="top:729px" role="img" aria-label="Thumbnail of a hotel building"></div>
    <h3 class="abs side-title" style="top:726px">THINGS TO DO IN EUROPE</h3>
    <p class="abs side-text" style="top:746px">Lorem ipsum dolor sit amet conse...</p>
    <div class="abs side-rule" style="top:801px"></div>

    <div class="abs side-img" style="top:812px" role="img" aria-label="Thumbnail of a hotel building"></div>
    <h3 class="abs side-title" style="top:809px">VISIT ROME</h3>
    <p class="abs side-text" style="top:830px">Lorem ipsum dolor sit amet conse...</p>
    <div class="abs side-rule" style="top:884px"></div>

    <div class="abs side-img" style="top:897px" role="img" aria-label="Thumbnail of a hotel building"></div>
    <h3 class="abs side-title" style="top:895px">VISIT ROME</h3>
    <p class="abs side-text" style="top:916px">Lorem ipsum dolor sit amet conse...</p>
    <div class="abs side-rule" style="top:975px"></div>

    <div class="abs side-img" style="top:990px" role="img" aria-label="Thumbnail of a hotel building"></div>
    <h3 class="abs side-title" style="top:984px">VISIT ROME</h3>
    <p class="abs side-text" style="top:1003px">Lorem ipsum dolor sit amet conse...</p>

    <a class="abs see-all">See All</a>
  </aside>

  <footer>
    <div class="abs footer-bar">
      <span style="left:22px">Home</span>
      <span style="left:79px">About Us</span>
      <span style="left:147px">Blog</span>
      <span style="left:195px">Forums</span>
      <span style="left:263px">Services</span>
      <span style="left:334px">Cities</span>
      <span style="left:386px">Testimonials</span>
      <span style="left:471px">Contact Us</span>
      <span style="left:624px">Follow us on</span>
    </div>
    <div class="abs social" style="left:800px" role="img" aria-label="Social network link"></div>
    <div class="abs social" style="left:835px" role="img" aria-label="RSS feed link"></div>
    <div class="abs social" style="left:869px" role="img" aria-label="Social network link"></div>
    <div class="abs social" style="left:904px" role="img" aria-label="Social network link"></div>
    <p class="abs copyright">COPYRIGHT @ TARROWTRAVELS.COM</p>
  </footer>

</body>
</html>
```